5 website banners (slides show)

We need 5 website sliding banners created for a website all about internet safety. The topics for each banner are:

Cyberbullying
Fraud
seniors
social networking

Sizes: 953 pixels x 281 pixels

I have stock images to use or feel free to use your own or one I can purchase from pixelharbor.example.

Industry/Entity Type

Internet

```html
<!DOCTYPE html>
<html lang="en">
<head>
<meta charset="utf-8">
<title>Cyberbullying Banner</title>
<link href="https://fonts.googleapis.com/css2?family=Open+Sans:ital,wght@0,400;0,600;0,700;1,400&display=swap" rel="stylesheet">
<style>
  :root {
    --bg-light: #f6f5f2;
    --bg-mid: #ecebe7;
    --border: #9a9a9a;
    --title: #111111;
    --body-text: #555555;
    --btn-top: #1f5aa8;
    --btn-bottom: #0d3a7a;
    --btn-border: #0a2e63;
    --btn-text: #ffffff;
    --dot-active: #111111;
    --dot-idle: #a3a3a3;
    --photo-tone: #cfe6ea;
    --photo-tone-deep: #b9dbe2;
  }
  * { margin: 0; padding: 0; box-sizing: border-box; }
  html, body { width: 1200px; height: 354px; overflow: hidden; background: #ffffff; }
  .banner {
    position: relative;
    width: 1200px;
    height: 354px;
    overflow: hidden;
    border-top: 2px solid var(--border);
    background: linear-gradient(110deg, var(--bg-mid) 0%, var(--bg-light) 45%, #fbfbfa 100%);
    font-family: "Open Sans", sans-serif;
  }
  .banner-photo {
    position: absolute;
    top: 0;
    right: 0;
    width: 530px;
    height: 100%;
    background: linear-gradient(90deg, var(--bg-light) 0%, var(--photo-tone) 30%, var(--photo-tone-deep) 100%);
  }
  .banner-content {
    position: absolute;
    left: 31px;
    top: 54px;
    width: 640px;
  }
  .banner-title {
    font-size: 34px;
    font-weight: 700;
    color: var(--title);
    letter-spacing: 0;
    line-height: 1.1;
  }
  .banner-text {
    margin-top: 12px;
    font-size: 18px;
    font-style: italic;
    color: var(--body-text);
    line-height: 28px;
    white-space: nowrap;
  }
  .learn-more {
    position: absolute;
    left: 31px;
    top: 239px;
    width: 175px;
    height: 44px;
    display: flex;
    align-items: center;
    justify-content: space-between;
    padding: 0 18px 0 22px;
    background: linear-gradient(180deg, var(--btn-top), var(--btn-bottom));
    border: 1px solid var(--btn-border);
    color: var(--btn-text);
    font-size: 16px;
    font-weight: 600;
    text-decoration: none;
    letter-spacing: 0.2px;
  }
  .slide-dots {
    position: absolute;
    left: 31px;
    top: 316px;
    display: flex;
    gap: 12px;
    list-style: none;
  }
  .slide-dots li { width: 13px; height: 13px; background: var(--dot-idle); }
  .slide-dots li.is-active { background: var(--dot-active); }
</style>
</head>
<body>
<section class="banner">
  <div class="banner-photo" role="img" aria-label="Photo of a group of teenage girls on a school floor with one girl sitting apart, looking upset"></div>
  <div class="banner-content">
    <h1 class="banner-title">CYBERBULLYING</h1>
    <p class="banner-text">Lorem Ipsum is simply dummy text of the printing and typesetting<br>industry. Lorem Ipsum has been the industry's standard dummy text<br>ever since the 1500s, when an unknown printer took a galley of type<br>and scrambled it to make a type specimen book.</p>
  </div>
  <a class="learn-more" href="#">LEARN MORE
    <svg width="22" height="18" viewBox="0 0 22 18" aria-hidden="true">
      <path d="M2 16 C3 9 8 6 13 6 V1 L21 8 L13 15 V10 C8 10 5 12 2 16 Z" fill="#ffffff"/>
    </svg>
  </a>
  <ul class="slide-dots">
    <li class="is-active"></li>
    <li></li>
    <li></li>
  </ul>
</section>
</body>
</html>
```